Corvane Capital Business Cards

These are professional business cards that are for my family office.
Put fake emails and phone numbers as of now until I finalize those components. This family office controls my families investments, assets, and future. The cards should be professional.
..
.
.
.
I just uploaded another variation of a logo I would like to see as a business card to I am inbeteen which logo to use

Target Market(s)

business

Industry/Entity Type

business

Contact Information for Business Card

Professional, wealth related, finance related.

Requirements
Must have
• Logo

```html
<!DOCTYPE html>
<html lang="en">
<head>
<meta charset="utf-8">
<title>Corvane Capital Business Cards</title>
<link href="https://fonts.googleapis.com/css2?family=Cinzel:wght@600&family=Arimo:wght@400&display=swap" rel="stylesheet">
<style>
  :root {
    --navy: #1a1e2c;
    --navy-deep: #151826;
    --silver: #a7a5a8;
    --paper: #ffffff;
    --stage: #e4e4e6;
    --ink-light: #f2f2f4;
  }
  * { box-sizing: border-box; margin: 0; padding: 0; }
  html, body { width: 1200px; height: 689px; overflow: hidden; background: var(--stage); }
  .canvas { position: relative; width: 1200px; height: 689px; }

  .card {
    position: absolute;
    top: 196px;
    width: 520px;
    height: 297px;
    border-radius: 18px;
    overflow: hidden;
    box-shadow: 0 6px 18px rgba(0,0,0,0.18);
  }

  /* Back */
  .card-back { left: 50px; background: var(--navy-deep); }
  .card-back .pattern-area { position: absolute; inset: 0; background: linear-gradient(135deg, #1d2233, #131624); }
  .card-back .back-mark {
    position: absolute; right: 26px; top: 78px;
    display: flex; align-items: center; gap: 8px;
  }
  .back-mark .mark-circle { width: 22px; height: 22px; border: 1.5px solid var(--ink-light); border-radius: 50%; }
  .back-mark .mark-name { font-family: "Cinzel", serif; font-weight: 600; font-size: 11px; color: var(--ink-light); letter-spacing: 0.5px; }

  /* Front */
  .card-front { left: 630px; background: var(--paper); }
  .card-front .shapes { position: absolute; inset: 0; }
  .card-front .brand {
    position: absolute; left: 318px; top: 66px; width: 186px;
    display: flex; flex-direction: column; align-items: center; gap: 14px;
  }
  .brand .brand-circle { width: 70px; height: 70px; border: 2.5px solid var(--navy); border-radius: 50%; }
  .brand .brand-name { font-family: "Cinzel", serif; font-weight: 600; font-size: 17px; color: var(--navy); letter-spacing: 0.8px; white-space: nowrap; }

  .person { position: absolute; left: 40px; top: 112px; color: var(--ink-light); }
  .person .name { font-family: "Cinzel", serif; font-weight: 600; font-size: 18px; letter-spacing: 0.5px; }
  .person .role { font-family: "Arimo", sans-serif; font-size: 10.5px; margin-top: 1px; }

  .contact { position: absolute; left: 50px; top: 172px; font-family: "Arimo", sans-serif; font-size: 11px; line-height: 14px; color: var(--ink-light); }
  .contact .address { margin-bottom: 9px; }
  .contact .row { display: flex; align-items: center; gap: 8px; }
  .contact .row svg { width: 9px; height: 9px; flex: none; }
</style>
</head>
<body>
<main class="canvas">

  <section class="card card-back" aria-label="Card back">
    <div class="pattern-area" role="img" aria-label="Tonal repeating monogram pattern across the dark card back"></div>
    <div class="back-mark">
      <span class="mark-circle"></span>
      <span class="mark-name">Corvane Capital</span>
    </div>
  </section>

  <section class="card card-front" aria-label="Card front">
    <svg class="shapes" viewBox="0 0 520 297" aria-hidden="true">
      <circle cx="130" cy="250" r="178" fill="var(--silver)"/>
      <circle cx="120" cy="250" r="175" fill="var(--navy)"/>
    </svg>

    <div class="brand">
      <span class="brand-circle"></span>
      <span class="brand-name">Corvane Capital</span>
    </div>

    <div class="person">
      <p class="name">Elias Marlow</p>
      <p class="role">President</p>
    </div>

    <div class="contact">
      <p class="address">4120 Larkspur Court<br>Halden, Canada 58213</p>
      <p class="row">
        <svg viewBox="0 0 10 10"><path d="M2 1l2 2-1 1.3c.6 1.2 1.5 2.1 2.7 2.7L7 6l2 2-1.3 1.5C4.5 9.2.8 5.5.5 2.3z" fill="currentColor"/></svg>
        555-210-4871
      </p>
      <p class="row">
        <svg viewBox="0 0 10 10"><rect x="2.5" y="0.5" width="5" height="9" rx="1" fill="none" stroke="currentColor"/><circle cx="5" cy="8" r="0.6" fill="currentColor"/></svg>
        555-310-6592
      </p>
      <p class="row">
        <svg viewBox="0 0 10 10"><rect x="0.5" y="2" width="9" height="6.5" fill="currentColor"/><path d="M0.5 2l4.5 3.5L9.5 2" fill="none" stroke="var(--navy)" stroke-width="0.9"/></svg>
        info@corvanecapital.com
      </p>
      <p class="row">
        <svg viewBox="0 0 10 10"><circle cx="5" cy="5" r="4.5" fill="currentColor"/><path d="M3 3.5c1 .3 1.5 1 1.2 2M6 7c.3-.8 1-1.2 1.8-1" stroke="var(--navy)" stroke-width="0.9" fill="none"/></svg>
        www.corvanecapital.com
      </p>
    </div>
  </section>

</main>
</body>
</html>
```